Hollendorf Business Card

This is the personal business card for Dr Mark Hollendorf and convers three area of his professional activity - all of them involve (foreign) languages:
o QRVB International Ltd - A translation company with 50 staff. Trades internationally
o WideHarbor Ltd - a global online auction marketplace for translation services (startup)
o Tonal Mosaic - cutting edge technology from the brain sciences which helps learners assimilate the sound patterns of a new language (startup)

Target Market(s)

The card needs to have a "cutting edge" feel - but for a fairly conservative audience - academics, investors.

Industry/Entity Type

Business

Requirements
Must have
• Text:
Dr Mark Hollendorf

Co-founder QRVB International Ltd (Language translation)
Founder WideHarbor Ltd (Translation marketplace)
Founder Tonal Mosaic (Language acquisition)

email: mark.oswin@velmora.co.nz
Phone: +64 21 596 3172
Twitter: @MarkOswin7

```html
<!DOCTYPE html>
<html lang="en">
<head>
<meta charset="utf-8">
<title>Mark Hollendorf – Business Card</title>
<link rel="stylesheet" href="https://fonts.googleapis.com/css2?family=Tinos&family=Lato:ital,wght@0,400;1,400&display=swap">
<style>
  :root {
    --card-bg: #ffffff;
    --panel-olive: #cccc9c;
    --accent-plum: #2e0b2f;
    --accent-grey: #c6c6c8;
    --ink: #1c1c1c;
  }
  html, body {
    margin: 0;
    padding: 0;
    overflow: hidden;
    background: var(--card-bg);
  }
  .card {
    position: relative;
    width: 1200px;
    height: 686px;
    background: var(--card-bg);
    overflow: hidden;
    font-family: "Lato", sans-serif;
    color: var(--ink);
  }
  .bar { position: absolute; }
  .bar--top-grey    { left: 600px; top: 36px;  width: 563px; height: 34px; background: var(--accent-grey); }
  .bar--top-plum    { left: 588px; top: 48px;  width: 545px; height: 9px;  background: var(--accent-plum); }
  .bar--bottom-plum { left: 525px; top: 600px; width: 638px; height: 16px; background: var(--accent-plum); }
  .bar--bottom-grey { left: 548px; top: 616px; width: 615px; height: 8px;  background: var(--accent-grey); }

  .panel {
    position: absolute;
    left: 36px;
    top: 34px;
    width: 511px;
    height: 616px;
    background: var(--panel-olive);
  }
  .panel__content {
    position: absolute;
    right: 41px;
    top: 118px;
    width: 440px;
    text-align: right;
  }
  .holder-name {
    margin: 0 0 22px;
    font-family: "Tinos", serif;
    font-weight: 400;
    font-size: 36px;
    line-height: 44px;
    letter-spacing: 0.5px;
  }
  .venture {
    margin: 0 0 33px;
    font-size: 16px;
    line-height: 20px;
  }
  .contact {
    margin-top: 34px;
    font-size: 29px;
    line-height: 40px;
  }
  .contact p { margin: 0; }

  .profile {
    position: absolute;
    left: 614px;
    top: 276px;
  }
  .profile__name {
    margin: 0 0 34px;
    font-style: italic;
    font-size: 27px;
    line-height: 32px;
    font-weight: 400;
  }
  .profile__field {
    margin: 0;
    font-size: 27px;
    line-height: 32px;
  }
</style>
</head>
<body>
  <div class="card">
    <div class="bar bar--top-grey"></div>
    <div class="bar bar--top-plum"></div>

    <section class="panel">
      <div class="panel__content">
        <h1 class="holder-name">MARK HOLLENDORF</h1>
        <p class="venture">Co-founder QRVB International Ltd (Language<br>Translation)</p>
        <p class="venture">Founder WideHarbor Ltd (Translation Marketplace)</p>
        <p class="venture">Founder Tonal Mosaic (Language Acquisition)</p>
        <div class="contact">
          <p>Phone: +64 21 596 3172</p>
          <p>Twitter: @MarkOswin7</p>
          <p>E-mail: mark.oswin@velmora.co.nz</p>
        </div>
      </div>
    </section>

    <section class="profile">
      <h2 class="profile__name">Dr. Mark Hollendorf</h2>
      <p class="profile__field">Profession in Foreign Languages</p>
    </section>

    <div class="bar bar--bottom-plum"></div>
    <div class="bar bar--bottom-grey"></div>
  </div>
</body>
</html>
```